Private Investigation Business Card Design

I need a business card for a new private investigation company named Brisk Inquiries. I perform mainly surveillance jobs, vehicle repossessions, document serves etc. The final design should aim for a professional look. The logo has a magnifying glass with stick man arms and legs and is in a running action to show the "Brisk" aspect of the name. If the colour scheme could remain the same as the website www.briskinquiries-demo.com.au with silvers,blacks and a couple electric blue highlights.
Industry/Entity Type
Business
Contact Information for Business Card
Morgan Kellaway
Brisk Inquiries
0487316204
PO Box 58, Carnwell NSW 2291
info@briskinquiries-demo.com.au
www.briskinquiries-demo.com.au
Look and feel

```html
<!DOCTYPE html>
<html lang="en">
<head>
<meta charset="utf-8">
<title>Brisk Inquiries – Business Card</title>
<link rel="stylesheet" href="https://fonts.googleapis.com/css2?family=Ubuntu:wght@400;500;700&display=swap">
<style>
  :root {
    --backdrop: #3b3b3b;
    --card: #fbfbfb;
    --ink: #222222;
    --ink-soft: #4a4a4a;
    --silver: #7a7a7a;
    --art-light: #f4f4f4;
    --art-mid: #d9d9d9;
    --art-dark: #9a9a9a;
  }
  * { margin: 0; padding: 0; box-sizing: border-box; }
  html, body {
    width: 1200px;
    height: 750px;
    overflow: hidden;
    background: var(--backdrop);
    font-family: "Ubuntu", sans-serif;
  }
  .card {
    position: absolute;
    top: 228px;
    width: 462px;
    height: 262px;
    background: var(--card);
    overflow: hidden;
  }
  .card--front { left: 124px; }
  .card--back { left: 618px; }

  .brand-name {
    font-family: "Ubuntu", sans-serif;
    font-weight: 500;
    color: var(--silver);
    white-space: nowrap;
    letter-spacing: 0.5px;
  }
  .card--front .brand-name {
    position: absolute;
    left: 30px;
    top: 28px;
    font-size: 27px;
  }

  .runner-art {
    position: absolute;
    left: 240px;
    top: 0;
    width: 222px;
    height: 262px;
    background: radial-gradient(ellipse at 60% 35%, var(--art-light) 0%, var(--art-mid) 55%, var(--art-dark) 100%);
  }

  .holder-name {
    position: absolute;
    left: 30px;
    top: 126px;
    font-size: 16px;
    font-weight: 700;
    color: var(--ink);
  }
  .postal {
    position: absolute;
    left: 30px;
    top: 156px;
    font-size: 11px;
    line-height: 14px;
    color: var(--ink-soft);
  }
  .contact-list {
    position: absolute;
    left: 30px;
    top: 192px;
    list-style: none;
  }
  .contact-list li {
    display: flex;
    align-items: center;
    height: 18px;
    font-size: 11px;
    color: var(--ink-soft);
  }
  .contact-list svg {
    width: 11px;
    height: 11px;
    margin-right: 6px;
    flex: none;
    fill: var(--ink);
  }

  .back-brand {
    position: absolute;
    left: 0;
    right: 0;
    top: 112px;
    display: flex;
    justify-content: center;
    align-items: center;
    gap: 10px;
  }
  .back-brand .brand-name { font-size: 27px; }
  .back-brand .brand-dot {
    width: 18px;
    height: 18px;
    border-radius: 50%;
    background: var(--art-mid);
  }
  .back-web {
    position: absolute;
    left: 0;
    right: 0;
    top: 218px;
    text-align: center;
    font-size: 10px;
    letter-spacing: 2px;
    color: var(--ink-soft);
  }
</style>
</head>
<body>
  <section class="card card--front">
    <div class="runner-art" role="img" aria-label="Illustration of a running figure with a magnifying glass for a head, with speed lines"></div>
    <div class="brand-name">Brisk Inquiries</div>
    <h1 class="holder-name">Morgan Kellaway</h1>
    <p class="postal">PO Box 58<br>Carnwell NSW 2291</p>
    <ul class="contact-list">
      <li>
        <svg viewBox="0 0 24 24" aria-hidden="true"><path d="M6.6 10.8a15.1 15.1 0 0 0 6.6 6.6l2.2-2.2a1 1 0 0 1 1-.25 11.4 11.4 0 0 0 3.6.57 1 1 0 0 1 1 1V20a1 1 0 0 1-1 1A17 17 0 0 1 3 4a1 1 0 0 1 1-1h3.5a1 1 0 0 1 1 1c0 1.25.2 2.45.57 3.57a1 1 0 0 1-.25 1z"/></svg>
        0487 316 204
      </li>
      <li>
        <svg viewBox="0 0 24 24" aria-hidden="true"><path d="M2 5h20v14H2z M4 7v.5l8 5 8-5V7z" fill-rule="evenodd"/></svg>
        info@briskinquiries-demo.com.au
      </li>
      <li>
        <svg viewBox="0 0 24 24" aria-hidden="true"><circle cx="12" cy="12" r="10"/></svg>
        www.briskinquiries-demo.com.au
      </li>
    </ul>
  </section>

  <section class="card card--back">
    <div class="back-brand">
      <span class="brand-name">Brisk Inquiries</span>
      <span class="brand-dot"></span>
    </div>
    <p class="back-web">www.briskinquiries-demo.com.au</p>
  </section>
</body>
</html>
```